Velmora Freightway Solutions Business cards

Would like a very unique design catchy but professional for business cards. Please use log provided.Marlon WellsCeo and Founder TransCon Logistix Solutions1-888-913-3225mwells@tlsolutionsus.comwww.tlsolutionsus.com

```html
<!DOCTYPE html>
<html lang="en">
<head>
<meta charset="utf-8">
<title>Velmora Freightway Solutions – Business Cards</title>
<link rel="stylesheet" href="https://fonts.googleapis.com/css2?family=Cinzel:wght@700&family=Open+Sans:wght@400&display=swap">
<style>
  :root {
    --page: #ecebe8;
    --card-white: #ffffff;
    --brand-red: #ec1f27;
    --brand-blue: #0c72bb;
    --map-tint: #2a86c8;
    --ink: #2b2b2b;
  }
  * { margin: 0; padding: 0; box-sizing: border-box; }
  html, body { width: 900px; height: 1200px; overflow: hidden; }
  body { background: var(--page); position: relative; font-family: "Open Sans", Arial, sans-serif; }

  .card {
    position: absolute;
    left: 87px;
    width: 733px;
    border-radius: 22px;
    overflow: hidden;
    box-shadow: 0 4px 12px rgba(0,0,0,0.25);
  }
  .card-front { top: 137px; height: 428px; background: var(--card-white); }
  .card-back { top: 633px; height: 429px; background: var(--brand-blue); }

  .holder { position: absolute; left: 52px; top: 52px; }
  .holder-name {
    font-family: "Cinzel", Georgia, serif;
    font-weight: 700;
    font-size: 25px;
    color: var(--brand-red);
    line-height: 1.1;
    letter-spacing: 0.5px;
  }
  .holder-role { font-size: 17px; color: var(--ink); line-height: 25px; margin-top: 4px; }

  .brand-front {
    position: absolute;
    left: 335px;
    top: 160px;
    width: 360px;
    text-align: center;
    font-family: "Cinzel", Georgia, serif;
    font-weight: 700;
    font-size: 25px;
    line-height: 32px;
    color: var(--brand-blue);
  }

  .contact-rule { position: absolute; left: 50px; top: 313px; width: 2px; height: 62px; background: var(--ink); }
  .contact-list { position: absolute; left: 64px; top: 307px; list-style: none; }
  .contact-list li { display: flex; align-items: center; height: 24px; font-size: 17px; color: var(--ink); }
  .contact-list svg { width: 12px; height: 12px; margin-right: 17px; fill: var(--brand-red); }
  .contact-list .domain { color: var(--brand-blue); }

  .band { position: absolute; bottom: 0; height: 28px; }
  .band-red { left: 0; width: 363px; background: var(--brand-red); }
  .band-blue { left: 369px; right: 0; background: var(--brand-blue); }

  .world-map {
    position: absolute;
    left: 95px;
    top: 55px;
    width: 540px;
    height: 340px;
    border-radius: 40px;
    background: radial-gradient(ellipse at center, var(--map-tint) 0%, rgba(42,134,200,0.35) 60%, rgba(42,134,200,0) 100%);
  }
  .brand-back {
    position: absolute;
    left: 0; right: 0;
    top: 150px;
    text-align: center;
    font-family: "Cinzel", Georgia, serif;
    font-weight: 700;
    font-size: 38px;
    line-height: 50px;
    color: var(--card-white);
  }
</style>
</head>
<body>

<section class="card card-front">
  <div class="holder">
    <h1 class="holder-name">Dorian Pike</h1>
    <p class="holder-role">Ceo and Founder<br>Velmora Freightway Solutions</p>
  </div>

  <div class="brand-front">Velmora Freightway<br>Solutions</div>

  <div class="contact-rule"></div>
  <ul class="contact-list">
    <li>
      <svg viewBox="0 0 24 24" aria-hidden="true"><path d="M6.6 10.8a15 15 0 0 0 6.6 6.6l2.2-2.2a1 1 0 0 1 1-.25 11.4 11.4 0 0 0 3.6.57 1 1 0 0 1 1 1V20a1 1 0 0 1-1 1A17 17 0 0 1 3 4a1 1 0 0 1 1-1h3.5a1 1 0 0 1 1 1c0 1.25.2 2.45.57 3.57a1 1 0 0 1-.25 1z"/></svg>
      1-888-470-6158
    </li>
    <li>
      <svg viewBox="0 0 24 24" aria-hidden="true"><path d="M2 5h20v2l-10 6L2 7z"/><path d="M2 9l10 6 10-6v10H2z"/></svg>
      dpike@<span class="domain">vfwayroutes</span>.com
    </li>
    <li>
      <svg viewBox="0 0 24 24" aria-hidden="true"><path d="M12 2a10 10 0 1 0 0 20 10 10 0 0 0 0-20zm6.9 6h-3a15 15 0 0 0-1.3-3.9A8 8 0 0 1 18.9 8zM12 4c.8 1.1 1.5 2.5 1.9 4h-3.8c.4-1.5 1.1-2.9 1.9-4zM4.3 14a8 8 0 0 1 0-4h3.3a16 16 0 0 0 0 4zm.8 2h3a15 15 0 0 0 1.3 3.9A8 8 0 0 1 5.1 16zm3-8h-3a8 8 0 0 1 4.3-3.9A15 15 0 0 0 8.1 8zM12 20c-.8-1.1-1.5-2.5-1.9-4h3.8c-.4 1.5-1.1 2.9-1.9 4zm2.3-6H9.7a14 14 0 0 1 0-4h4.6a14 14 0 0 1 0 4zm.3 5.9a15 15 0 0 0 1.3-3.9h3a8 8 0 0 1-4.3 3.9zM16.4 14a16 16 0 0 0 0-4h3.3a8 8 0 0 1 0 4z"/></svg>
      www.<span class="domain">vfwayroutes</span>.com
    </li>
  </ul>

  <div class="band band-red"></div>
  <div class="band band-blue"></div>
</section>

<section class="card card-back">
  <div class="world-map" role="img" aria-label="Faint world map in lighter blue"></div>
  <div class="brand-back">Velmora Freightway<br>Solutions</div>
</section>

</body>
</html>
```